Billboard design for high performance real estate broker

I need a new design for a billboard representing my Real Estate Company. The company name is Marla Quentwood Real Estate. I want to include my photo. Other necessary items are my phone number :
418.562.9071 along with Homeguild brand logo and Open Dwelling logo. I will send my photos (you and choose whichever works best and you can crop as needed) and my current company logo, but I am open to changes on that item. I need a good tag line on the billboard. It is located on a busy street so I don’t need a lot of text in the tag line. I think you can probably get the homeguild brand logo and open dwelling logo online. If not, I can send them. I have been in the industry almost 20 years so I am very experienced. I represent buyers and sellers. Most of my clients are repeat clients and referrals. Just trying to stay top of mind for anyone wanting to buy or sell real estate. I handle residential, land and some commercial sales.

Target Market(s)

Could be first time homebuyer or someone looking for buy or sell their luxury home

Industry/Entity Type

Real Estate

Colors
0054AA
0677BA
7BADD7
CADEEF
E8F1F8

Requirements
Must have
• Attention getting with catchy tag line
Nice to have
• Nice pop to catch drivers attention
Should not have
• Not too much wording as the viewer will be speeding by the sign

```html
<!DOCTYPE html>
<html lang="en">
<head>
<meta charset="utf-8">
<title>Marla Quentwood Real Estate – Billboard</title>
<link href="https://fonts.googleapis.com/css2?family=Kaushan+Script&family=Montserrat:wght@600;700;800;900&display=swap" rel="stylesheet">
<style>
  :root{
    --navy:#1f3574;
    --blue:#0054aa;
    --blue-mid:#0677ba;
    --blue-soft:#7badd7;
    --blue-pale:#cadeef;
    --blue-mist:#e8f1f8;
    --ink:#1b2232;
    --bar:#3d3f43;
    --stage:#e6e7ea;
    --white:#ffffff;
  }
  *{box-sizing:border-box;margin:0;padding:0}
  html,body{width:938px;height:1200px;overflow:hidden}
  body{background:var(--stage);position:relative;font-family:"Montserrat",sans-serif}

  .billboard{
    position:absolute;left:39px;top:385px;width:860px;height:430px;
    background:linear-gradient(180deg,#f1f2f4 0%,#ffffff 55%);
    overflow:hidden;box-shadow:0 14px 28px rgba(0,0,0,.3);
  }
  .billboard__dots{
    position:absolute;left:0;top:0;width:860px;height:200px;
    background-image:radial-gradient(circle,#dcdfe4 1.3px,transparent 1.6px);
    background-size:11px 11px;opacity:.8;
    -webkit-mask-image:linear-gradient(180deg,#000 0%,transparent 100%);
    mask-image:linear-gradient(180deg,#000 0%,transparent 100%);
  }
  .base{position:absolute;left:0;top:0}

  .headline{font-weight:900}
  .headline__row{position:absolute;left:40px;display:flex;align-items:baseline;line-height:1}
  .headline__row--buy{top:21px}
  .headline__row--sell{top:117px}
  .headline__word{
    font-size:112px;letter-spacing:-3px;
    background:linear-gradient(180deg,var(--navy) 0%,#23408a 100%);
    -webkit-background-clip:text;background-clip:text;color:transparent;
    filter:drop-shadow(5px 5px 0 #d4d6db);
  }
  .headline__word--sell{
    background:linear-gradient(180deg,var(--blue) 0%,#0a4c9c 100%);
    -webkit-background-clip:text;background-clip:text;
  }
  .headline__or{
    margin-left:6px;font-size:40px;font-weight:800;
    color:var(--navy);filter:drop-shadow(3px 3px 0 #d4d6db);
  }

  .services{
    position:absolute;left:43px;top:240px;width:283px;height:75px;
    border:1.5px solid var(--blue);border-left:8px solid var(--blue);background:var(--white);
    padding:11px 0 0 15px;font-weight:800;font-size:19.5px;line-height:1.27;color:var(--ink);
  }

  .portrait{
    position:absolute;left:340px;top:11px;width:225px;height:322px;
    border-radius:90px 90px 0 0;
    background:linear-gradient(180deg,#efe6d6 0%,#e2c9a0 38%,#9fa6cf 58%,#2b55c8 72%,#1f43b0 100%);
  }

  .experience{position:absolute;left:548px;top:40px;width:222px;text-align:center;color:var(--navy)}
  .experience__script{
    display:block;font-family:"Kaushan Script",cursive;line-height:.95;
    text-shadow:2px 2px 0 #fff,-2px -2px 0 #fff,2px -2px 0 #fff,-2px 2px 0 #fff,4px 4px 0 var(--blue-mid);
  }
  .experience__script--num{font-size:56px;margin-left:-40px}
  .experience__script--years{font-size:58px;margin-top:-6px}
  .experience__word{display:block;font-weight:700;font-size:22px;margin-top:-6px;color:var(--blue)}

  .badge{position:absolute;left:786px;width:35px;height:35px;background:var(--ink);border-radius:2px}
  .badge--one{top:34px}
  .badge--two{top:98px;height:28px;background:transparent;border:5px solid var(--ink)}

  .brand{position:absolute;left:560px;top:258px;display:flex;align-items:center;gap:14px}
  .brand__dot{width:44px;height:44px;border-radius:50%;background:var(--blue-pale);border:2px solid var(--navy);flex:none}
  .brand__name{font-weight:800;font-size:18px;line-height:1.12;color:var(--navy)}

  .phone{
    position:absolute;left:102px;top:332px;width:656px;height:80px;border-radius:40px;
    background:var(--blue);display:flex;align-items:center;padding-left:29px;gap:20px;
  }
  .phone__icon{width:56px;height:56px;flex:none}
  .phone__number{font-weight:800;font-size:80px;letter-spacing:-1px;color:var(--white);line-height:1}
</style>
</head>
<body>
  <section class="billboard" aria-label="Marla Quentwood Real Estate billboard">
    <div class="billboard__dots"></div>

    <svg class="base" width="860" height="430" viewBox="0 0 860 430" aria-hidden="true">
      <polygon points="340,333 680,226 852,288 852,333" fill="#ffffff"/>
      <polygon points="38,411 73,375 800,375 835,411" fill="var(--bar)"/>
      <polygon points="38,411 73,375 80,375 48,411" fill="var(--blue)"/>
      <polygon points="835,411 800,375 793,375 825,411" fill="var(--blue)"/>
      <rect x="0" y="411" width="860" height="19" fill="var(--bar)"/>
    </svg>

    <div class="portrait" role="img" aria-label="Portrait photo of the agent wearing a royal blue blouse"></div>

    <h1 class="headline">
      <span class="headline__row headline__row--buy">
        <span class="headline__word">BUY</span><span class="headline__or">or</span>
      </span>
      <span class="headline__row headline__row--sell">
        <span class="headline__word headline__word--sell">SELL</span>
      </span>
    </h1>

    <p class="services">Residential,<br>Land &amp; Commercial</p>

    <p class="experience">
      <span class="experience__script experience__script--num">20</span>
      <span class="experience__script experience__script--years">years of</span>
      <span class="experience__word">experience</span>
    </p>

    <div class="badge badge--one" role="img" aria-label="Homeguild member badge"></div>
    <div class="badge badge--two" role="img" aria-label="Open Dwelling badge"></div>

    <div class="brand">
      <span class="brand__dot"></span>
      <span class="brand__name">Marla Quentwood<br>Real Estate</span>
    </div>

    <div class="phone">
      <svg class="phone__icon" viewBox="0 0 56 56" aria-hidden="true">
        <circle cx="28" cy="28" r="27" fill="#ffffff"/>
        <circle cx="28" cy="28" r="22" fill="var(--navy)"/>
        <path d="M21 17c1.5-1 3-.8 3.8.6l2 3.6c.6 1.2.2 2.4-.9 3.1l-1.3.8c.9 2.6 2.6 4.7 4.9 6.2l1.2-.9c1-.8 2.4-.6 3.2.4l2.5 3.2c.9 1.2.6 2.7-.7 3.6l-1.6 1.1C30.5 45 17 32 19.5 18.5z" fill="#ffffff"/>
      </svg>
      <span class="phone__number">418.562.9071</span>
    </div>
  </section>
</body>
</html>
```